Dietary supplement, Clean and simple.

Hi,
I’d like to talk about the project,

About us:
We are a dietary supplement (Vitamins, Minerals, amino acids etc.) company.
The goal is to have about 25 products at the end of this year. However, for this goal to be achieved we need a good label design to make our products represent our company values.
I’ll be here every day supporting your questions, we are fully committed to making the highest/best quality/customer experience possible.

About the design and our values:
- Professional (We are in the industry of professionalism and expertise. I would love to show we are competent at this, Id. Like to have the labels looks like we have done our research.)
- Efficient (White spacing, good use of the space available.)
- Simple (Straight forward, in 5 seconds they have to know what the product they have is/how functions. We’re trying to simplify it for the consumer.
- No distractions (the only visually “distracting” factor can be the vector art.)

The guidelines:
The goal is to have a universal design, with one element that changes (Vector art). I’ll attach a file/multiple files I think can show some visuals on what I’m looking for, and what parts of the design I think are good/bad.

Label size: 69x155mm (Front is 77.5mm)

Design whatever you think fits our image. You’re the design expert, all I care about is that it fits our company standards/image.

Use this color/font.
Font: Sans Serif
Main company color is Mind green #237D62 (Use this color for something in the design.)

What I thought would be cool/might looks ugly, who knows:
1. The front of the label: Should have 1 vector art, preferably in the top right corner. (That looks good in multiple colors. The vector can have multiple areas to color, I would prefer 2 main colors in the vector art. The interchangeable colors are used for multiple kinds of products.)
2. Text/product information on the left. The text that will have to be displayed:
- Product name for instance “Magnesium + B6”
- Description for the product for instance “Magnesium with ginger taste”
- Company name or logo. (Add ® behind it. We are soon to be trademark registered.)
3. We need to show the "daily intake" amount on the front and also the amount in the complete bottle. For instance, “Daily intake 1 capsule, 60 capsules”.
• You don’t have to design the backside of the label. After I chose a design, I’d like to chat and give specific information on what areas need to be assigned where. (Too complex because of the law.)
Updates

Hi, Please make the deadline 31 days total. I want designers to have the time to design. And not be rushed to finish it.

I want to extend the deadline because i feel like a slightly more medical look would be interesting. Hope you can come up with something!!

Target Market(s)

Dietary supplement consumers

Industry/Entity Type

Dietary supplements

Font styles to use
Sans Serif

Colors

Designer to choose colors to be used in the design.

Requirements
Must have
• Trademark icon "®" has to be at the top right after the company logo(text of logo)/name.

```html
<!DOCTYPE html>
<html lang="en">
<head>
<meta charset="UTF-8">
<title>Noble Calm – Magnesium + B6 Label Range</title>
<link href="https://fonts.googleapis.com/css2?family=Archivo:wght@400;600;700&display=swap" rel="stylesheet">
<style>
  :root {
    --page: #ffffff;
    --label: #ececec;
    --ink: #3a3a3a;
    --ink-soft: #555555;
    --brand-green: #237D62;

    --coral-1: #ecd8cc;
    --coral-2: #f0b79a;
    --coral-3: #f09a72;
    --coral-4: #ee5a40;
    --coral-5: #d8452f;

    --plum-1: #efd4ec;
    --plum-2: #dca0d6;
    --plum-3: #c455b6;
    --plum-4: #4a1236;
    --plum-5: #25051a;

    --copper-1: #f0ddd2;
    --copper-2: #e6b79c;
    --copper-3: #d89a78;
    --copper-4: #c27a48;
    --copper-5: #8a3e10;
  }
  * { box-sizing: border-box; margin: 0; padding: 0; }
  html, body {
    width: 1200px; height: 873px; overflow: hidden;
    background: var(--page);
    font-family: "Archivo", Arial, sans-serif;
  }
  .range {
    display: flex; gap: 30px;
    position: absolute; left: 60px; top: 226px;
  }
  .label {
    position: relative;
    width: 340px; height: 420px;
    background: linear-gradient(160deg, #f1f1f1 0%, var(--label) 60%, #e2e2e2 100%);
    overflow: hidden;
  }
  .label-art { position: absolute; top: 0; right: 0; width: 340px; height: 420px; }
  .brand {
    position: absolute; left: 36px; top: 146px;
    display: flex; align-items: center; gap: 7px;
    color: var(--brand-green);
    font-weight: 700; font-size: 21px; letter-spacing: 0.3px; line-height: 1;
    white-space: nowrap;
  }
  .brand-dot { width: 12px; height: 12px; border-radius: 50%; background: var(--brand-green); flex: none; }
  .brand-reg { font-size: 10px; align-self: flex-start; margin-left: -4px; margin-top: -3px; color: var(--ink); font-weight: 400; }
  .product-name {
    position: absolute; left: 36px; top: 236px;
    font-size: 22px; font-weight: 600; color: var(--ink); letter-spacing: 0.2px;
  }
  .product-desc {
    position: absolute; left: 37px; top: 266px;
    font-size: 7.5px; letter-spacing: 1.6px; color: var(--ink-soft); text-transform: uppercase;
  }
  .count { position: absolute; left: 36px; top: 296px; color: var(--ink); }
  .count-num { font-size: 14px; font-weight: 600; line-height: 1; }
  .count-unit { font-size: 6px; text-transform: uppercase; color: var(--ink-soft); margin-top: 2px; }
  .rule { position: absolute; left: 37px; top: 332px; width: 22px; height: 2px; }
  .intake { position: absolute; left: 36px; top: 342px; color: var(--ink); }
  .intake-amount { font-size: 15px; font-weight: 600; line-height: 1; }
  .intake-unit { font-size: 6px; text-transform: uppercase; color: var(--ink-soft); margin-top: 2px; }
  .label--coral .rule { background: var(--coral-4); }
  .label--plum .rule { background: var(--plum-4); }
  .label--copper .rule { background: var(--copper-4); }
</style>
</head>
<body>
<main class="range">

  <section class="label label--coral">
    <svg class="label-art" viewBox="0 0 340 420" aria-hidden="true">
      <defs>
        <linearGradient id="coralCore" x1="0" y1="0" x2="1" y2="0">
          <stop offset="0" stop-color="var(--coral-4)"/><stop offset="1" stop-color="var(--coral-5)"/>
        </linearGradient>
      </defs>
      <circle cx="345" cy="-10" r="210" fill="var(--coral-1)" opacity="0.8"/>
      <circle cx="345" cy="-10" r="190" fill="var(--coral-2)"/>
      <circle cx="345" cy="-10" r="170" fill="var(--coral-3)"/>
      <circle cx="345" cy="-10" r="150" fill="url(#coralCore)"/>
    </svg>
    <div class="brand"><span class="brand-dot"></span>NOBLE CALM<span class="brand-reg">®</span></div>
    <h2 class="product-name">MAGNESIUM + B6</h2>
    <p class="product-desc">Magnesium with ginger taste</p>
    <div class="count"><div class="count-num">60</div><div class="count-unit">Capsules</div></div>
    <div class="rule"></div>
    <div class="intake"><div class="intake-amount">1 CAPSULE</div><div class="intake-unit">Daily intake</div></div>
  </section>

  <section class="label label--plum">
    <svg class="label-art" viewBox="0 0 340 420" aria-hidden="true">
      <defs>
        <linearGradient id="plumCore" x1="0" y1="0" x2="1" y2="1">
          <stop offset="0" stop-color="var(--plum-4)"/><stop offset="1" stop-color="var(--plum-5)"/>
        </linearGradient>
      </defs>
      <circle cx="345" cy="-10" r="210" fill="var(--plum-1)"/>
      <circle cx="345" cy="-10" r="190" fill="var(--plum-2)"/>
      <circle cx="345" cy="-10" r="170" fill="var(--plum-3)"/>
      <circle cx="345" cy="-10" r="150" fill="url(#plumCore)"/>
    </svg>
    <div class="brand"><span class="brand-dot"></span>NOBLE CALM<span class="brand-reg">®</span></div>
    <h2 class="product-name">MAGNESIUM + B6</h2>
    <p class="product-desc">Magnesium with ginger taste</p>
    <div class="count"><div class="count-num">60</div><div class="count-unit">Capsules</div></div>
    <div class="rule"></div>
    <div class="intake"><div class="intake-amount">1 CAPSULE</div><div class="intake-unit">Daily intake</div></div>
  </section>

  <section class="label label--copper">
    <svg class="label-art" viewBox="0 0 340 420" aria-hidden="true">
      <defs>
        <linearGradient id="copperCore" x1="0" y1="0" x2="1" y2="0">
          <stop offset="0" stop-color="var(--copper-4)"/><stop offset="1" stop-color="var(--copper-5)"/>
        </linearGradient>
      </defs>
      <circle cx="345" cy="-10" r="210" fill="var(--copper-1)"/>
      <circle cx="345" cy="-10" r="190" fill="var(--copper-2)"/>
      <circle cx="345" cy="-10" r="170" fill="var(--copper-3)"/>
      <circle cx="345" cy="-10" r="150" fill="url(#copperCore)"/>
    </svg>
    <div class="brand"><span class="brand-dot"></span>NOBLE CALM<span class="brand-reg">®</span></div>
    <h2 class="product-name">MAGNESIUM + B6</h2>
    <p class="product-desc">Magnesium with ginger taste</p>
    <div class="count"><div class="count-num">60</div><div class="count-unit">Capsules</div></div>
    <div class="rule"></div>
    <div class="intake"><div class="intake-amount">1 CAPSULE</div><div class="intake-unit">Daily intake</div></div>
  </section>

</main>
</body>
</html>
```